Web Design for company in the healthcare industry

We need a web design for a new company in the healthcare industry (telehealth) which allows patients to schedule appointments at their convenience, view and monitor their results, and consult with specialists that fit their requirements. The aim is to help patients take charge of their own health.

We already have a logo (attached) and are working with a developer who will do all the back end programming once the design is ready. Apart from the colours in the logo, we think shades of gray would work well.

Target Market(s)

I imagine the vast majority would be professionals from 30-50 years old.

Industry/Entity Type

Health And Wellness

Number of Pages Required

4 page

Requirements
Must have
• Hand-sketched graphics, particularly on landing page.
Should not have
• We don't want any photographs of people

```html
<!DOCTYPE html>
<html lang="en">
<head>
<meta charset="utf-8">
<title>Medora — Take Charge of Your Health</title>
<link href="https://fonts.googleapis.com/css2?family=Montserrat:wght@400;600;700&family=Open+Sans:wght@400;600&display=swap" rel="stylesheet">
<style>
:root{
  --blue:#1d5c9e;
  --blue-dark:#174e88;
  --blue-deep:#123f70;
  --green:#8cc63f;
  --green-dark:#76ad2c;
  --grey-bg:#eeeff1;
  --grey-line:#d7d9dc;
  --grey-text:#7a7d82;
  --ink:#2f3338;
  --white:#ffffff;
  --btn-grey:#5d6168;
}
*{box-sizing:border-box;margin:0;padding:0}
html,body{width:1200px;height:2224px;overflow:hidden}
body{font-family:"Open Sans",Arial,sans-serif;color:var(--ink);background:var(--white);position:relative}
h1,h2,h3,h4{font-family:"Montserrat",Arial,sans-serif}

/* header */
.site-header{height:118px;display:flex;align-items:center;justify-content:space-between;padding:0 100px}
.brand{display:flex;align-items:center;gap:10px;font-family:"Montserrat",sans-serif;font-weight:700;font-size:40px;color:var(--blue);letter-spacing:-0.5px}
.brand-dot{width:18px;height:18px;border-radius:50%;background:var(--green)}
.main-nav{display:flex;gap:34px;font-family:"Montserrat",sans-serif;font-size:14px}
.main-nav a{color:var(--blue);text-decoration:none;padding-bottom:8px}
.main-nav a.is-active{color:var(--green);border-bottom:2px solid var(--green)}

/* hero */
.hero{height:642px;background:var(--grey-bg);text-align:center;padding-top:30px;position:relative}
.section-title{font-size:34px;font-weight:600;color:var(--blue);letter-spacing:0.5px}
.hero .section-title{font-size:38px}
.pulse{display:block;margin:10px auto 0}
.steps{position:relative;width:980px;margin:40px auto 0;display:grid;grid-template-columns:repeat(4,1fr)}
.steps-arrows{position:absolute;left:0;top:0}
.step{display:flex;flex-direction:column;align-items:center;position:relative}
.step-icon{width:96px;height:96px;border-radius:50%;background:var(--white);border:2px solid var(--grey-line);display:flex;align-items:center;justify-content:center}
.step-icon span{width:52px;height:52px;border-radius:50%;background:linear-gradient(135deg,#cfe3f3,#dceec6)}
.step h3{margin-top:26px;font-size:17px;font-weight:600;color:var(--ink);line-height:1.25;min-height:44px}
.step p{margin-top:12px;font-size:12px;color:var(--grey-text);line-height:1.6;width:190px}
.btn{display:inline-block;font-family:"Montserrat",sans-serif;font-size:11px;font-weight:600;color:var(--white);text-transform:uppercase;letter-spacing:0.5px;border:none}
.btn-start{margin-top:56px;background:var(--green);padding:12px 24px}

/* packages */
.packages{padding-top:62px;text-align:center;position:relative;height:570px}
.package-row{width:1000px;margin:44px auto 0;display:grid;grid-template-columns:repeat(3,1fr);gap:22px}
.package{background:var(--white);border:1px solid var(--grey-line);height:360px;padding-top:26px}
.package.is-featured{box-shadow:0 6px 22px rgba(0,0,0,.16);border-color:transparent}
.package h4{font-size:16px;font-weight:600;color:var(--ink)}
.package.is-featured h4{color:var(--blue)}
.package-band{margin-top:22px;height:110px;background:#f4f5f6;display:flex;align-items:center;justify-content:center}
.package-icon{width:92px;height:92px;border-radius:50%;background:var(--white);border:2px solid var(--grey-line);display:flex;align-items:center;justify-content:center}
.package.is-featured .package-icon{background:var(--blue);border-color:var(--blue)}
.package-icon span{width:40px;height:40px;border-radius:50%;background:#c9ccd0}
.package.is-featured .package-icon span{background:#6d9fd0}
.package p{font-size:12px;color:var(--grey-text);line-height:1.6;width:240px;margin:30px auto 0}
.price{font-family:"Montserrat",sans-serif;font-size:15px;color:var(--blue);margin-top:14px}
.package-actions{display:flex;justify-content:center;gap:6px;margin-top:16px}
.btn-small{padding:7px 14px;font-size:9px;background:var(--btn-grey)}
.btn-small.btn-green{background:var(--green)}
.package.is-featured .btn-small.btn-dark{background:var(--blue)}
.carousel-arrow{position:absolute;top:340px}
.carousel-arrow.left{left:52px}
.carousel-arrow.right{right:52px}

/* specialists */
.specialists{text-align:center;height:512px;padding-top:40px}
.specialist-row{width:1000px;margin:44px auto 0;display:grid;grid-template-columns:repeat(4,1fr);gap:20px}
.specialist{background:#f1f2f3;height:284px;padding-top:28px}
.specialist.is-featured{background:var(--green)}
.specialist-photo{width:128px;height:128px;border-radius:50%;margin:0 auto;background:linear-gradient(160deg,#dfe3e8,#b8bec6);border:4px solid var(--white)}
.specialist h4{margin-top:16px;font-size:15px;font-weight:600;color:var(--blue);text-transform:uppercase}
.specialist.is-featured h4{color:var(--white)}
.specialist .role{font-size:11px;color:var(--grey-text);margin-top:4px}
.specialist.is-featured .role{color:#eef7e1}
.btn-know{margin-top:16px;padding:7px 16px;font-size:9px;background:var(--green)}
.specialist.is-featured .btn-know{background:var(--blue)}
.dots{display:flex;justify-content:center;gap:8px;margin-top:26px}
.dots i{width:10px;height:10px;border-radius:50%;border:1.5px solid var(--blue)}
.dots i.on{background:var(--blue)}

/* footer */
.site-footer{position:absolute;left:0;top:1800px;width:1200px;height:424px;background:var(--blue);color:var(--white)}
.footer-cols{position:relative;height:352px}
.footer-cols h4{font-size:13px;font-weight:600;text-transform:uppercase;letter-spacing:.5px}
.quick-links{position:absolute;left:100px;top:40px}
.quick-links ul{list-style:none;margin-top:14px;font-size:12px;line-height:1.75}
.quick-links li::before{content:"›";margin-right:8px;color:var(--green)}
.footer-map{position:absolute;left:310px;top:52px;width:170px;height:150px;background:linear-gradient(135deg,#e6ebe2,#cfd8de)}
.touch{position:absolute;left:510px;top:40px;width:240px}
.touch p{font-size:11px;line-height:1.6;margin-top:12px;color:#d9e6f4}
.touch ul{list-style:none;margin-top:16px;font-size:11px;line-height:2;color:#e8f0f8}
.touch li{display:flex;align-items:center;gap:8px}
.contact-now{position:absolute;left:810px;top:40px;width:290px}
.contact-form{display:grid;grid-template-columns:1fr 1fr;gap:6px;margin-top:14px}
.field{background:var(--white);height:26px;font-size:10px;color:#9aa0a6;padding:6px 8px}
.field.message{grid-column:2;grid-row:1 / span 3;height:90px}
.btn-submit{justify-self:end;grid-column:2;background:var(--green);padding:7px 16px;font-size:9px;margin-top:8px}
.footer-bar{height:72px;background:var(--blue-deep);display:flex;align-items:center;justify-content:space-between;padding:0 100px;font-size:11px;color:#cbd8e6}
.socials{display:flex;gap:10px}
.socials i{width:20px;height:20px;border-radius:50%;background:#3b72ad}
</style>
</head>
<body>

<header class="site-header">
  <div class="brand">Medora<span class="brand-dot"></span></div>
  <nav class="main-nav">
    <a class="is-active" href="#">Home</a>
    <a href="#">Health Packages</a>
    <a href="#">Appointments</a>
    <a href="#">Specialists</a>
    <a href="#">Contact Us</a>
  </nav>
</header>

<section class="hero">
  <h1 class="section-title">TAKE CHARGE OF YOUR HEALTH</h1>
  <div class="steps">
    <svg class="steps-arrows" width="980" height="100" viewBox="0 0 980 100" fill="none" stroke="#8cc63f" stroke-width="2" stroke-dasharray="4 5">
      <path d="M175 40 Q245 -5 315 40"/><path d="M307 34 l9 6 -10 3" stroke-dasharray="none"/>
      <path d="M420 40 Q490 -5 560 40"/><path d="M552 34 l9 6 -10 3" stroke-dasharray="none"/>
      <path d="M665 40 Q735 -5 805 40"/><path d="M797 34 l9 6 -10 3" stroke-dasharray="none"/>
    </svg>
    <div class="step">
      <div class="step-icon"><span role="img" aria-label="Sketched shopping basket icon"></span></div>
      <h3>Select a package</h3>
      <p>Browse our health packages and pick the one that fits your needs.</p>
    </div>
    <div class="step">
      <div class="step-icon"><span role="img" aria-label="Sketched calendar icon"></span></div>
      <h3>Schedule an appointment<br>at your convenience</h3>
      <p>Choose a time and place that suits your busy weekly schedule.</p>
    </div>
    <div class="step">
      <div class="step-icon"><span role="img" aria-label="Sketched results report icon"></span></div>
      <h3>Get your result back</h3>
      <p>Receive your results online and track them from your own dashboard.</p>
    </div>
    <div class="step">
      <div class="step-icon"><span role="img" aria-label="Sketched healthy person icon"></span></div>
      <h3>A healthier you</h3>
      <p>Follow expert advice and take charge of your long term wellbeing.</p>
    </div>
  </div>
  <a class="btn btn-start">Get Start Now</a>
</section>

<section class="packages">
  <h2 class="section-title">HEALTH PACKAGES</h2>
  <svg class="pulse" width="120" height="18" viewBox="0 0 120 18" fill="none" stroke="#8cc63f" stroke-width="2"><path d="M0 9 H46 L52 2 L58 16 L64 4 L70 9 H120"/></svg>
  <svg class="carousel-arrow left" width="14" height="26" viewBox="0 0 14 26" fill="none" stroke="#9aa0a6" stroke-width="2"><path d="M12 2 L2 13 L12 24"/></svg>
  <svg class="carousel-arrow right" width="14" height="26" viewBox="0 0 14 26" fill="none" stroke="#9aa0a6" stroke-width="2"><path d="M2 2 L12 13 L2 24"/></svg>
  <div class="package-row">
    <article class="package is-featured">
      <h4>Anti-Ageing, Men</h4>
      <div class="package-band"><div class="package-icon"><span role="img" aria-label="Sketched man profile icon"></span></div></div>
      <p>Full screening for men focused on healthy ageing and vitality.</p>
      <div class="price">$199.00</div>
      <div class="package-actions"><a class="btn btn-small btn-green">Book Now</a><a class="btn btn-small btn-dark">More Details</a></div>
    </article>
    <article class="package">
      <h4>Sports &amp; Performance</h4>
      <div class="package-band"><div class="package-icon"><span role="img" aria-label="Sketched athlete icon"></span></div></div>
      <p>Tests tailored for active people who train and compete often.</p>
      <div class="price">$442.00</div>
      <div class="package-actions"><a class="btn btn-small btn-green">Book Now</a><a class="btn btn-small">More Details</a></div>
    </article>
    <article class="package">
      <h4>Heart Disease</h4>
      <div class="package-band"><div class="package-icon"><span role="img" aria-label="Sketched heart and stethoscope icon"></span></div></div>
      <p>Checks for heart health, blood pressure and cholesterol levels.</p>
      <div class="price">$110.00</div>
      <div class="package-actions"><a class="btn btn-small btn-green">Book Now</a><a class="btn btn-small">More Details</a></div>
    </article>
  </div>
</section>

<section class="specialists">
  <h2 class="section-title">OUR SPECIALISTS</h2>
  <svg class="pulse" width="120" height="18" viewBox="0 0 120 18" fill="none" stroke="#8cc63f" stroke-width="2"><path d="M0 9 H46 L52 2 L58 16 L64 4 L70 9 H120"/></svg>
  <div class="specialist-row">
    <article class="specialist is-featured">
      <div class="specialist-photo" role="img" aria-label="Portrait of the specialist"></div>
      <h4>Dr. Nora Vale</h4>
      <div class="role">Senior Cardio Specialist</div>
      <a class="btn btn-know">Know More ›</a>
    </article>
    <article class="specialist">
      <div class="specialist-photo" role="img" aria-label="Portrait of the specialist"></div>
      <h4>Dr. Owen Marsh</h4>
      <div class="role">Senior Cardio Specialist</div>
      <a class="btn btn-know">Know More ›</a>
    </article>
    <article class="specialist">
      <div class="specialist-photo" role="img" aria-label="Portrait of the specialist"></div>
      <h4>Dr. Lena Brook</h4>
      <div class="role">Senior Cardio Specialist</div>
      <a class="btn btn-know">Know More ›</a>
    </article>
    <article class="specialist">
      <div class="specialist-photo" role="img" aria-label="Portrait of the specialist"></div>
      <h4>Dr. Milo Grant</h4>
      <div class="role">Senior Cardio Specialist</div>
      <a class="btn btn-know">Know More ›</a>
    </article>
  </div>
  <div class="dots"><i class="on"></i><i></i><i></i></div>
</section>

<footer class="site-footer">
  <div class="footer-cols">
    <div class="quick-links">
      <h4>Quick Links</h4>
      <ul><li>Home</li><li>Health Packages</li><li>Appointment</li><li>Specialist</li><li>Contact Us</li></ul>
    </div>
    <div class="footer-map" role="img" aria-label="Map showing the clinic location"></div>
    <div class="touch">
      <h4>Get in Touch</h4>
      <p>Reach our care team any day for help with bookings.</p>
      <ul>
        <li><svg width="12" height="14" viewBox="0 0 12 14"><path d="M6 0a5 5 0 0 0-5 5c0 4 5 9 5 9s5-5 5-9a5 5 0 0 0-5-5z" fill="#8cc63f"/></svg>24 Harbor Lane, Westfield 40217</li>
        <li><svg width="12" height="12" viewBox="0 0 12 12"><path d="M2 1l2 0 1 3-1.5 1a7 7 0 0 0 3.5 3.5L8 7l3 1v2a1 1 0 0 1-1 1A9 9 0 0 1 1 2a1 1 0 0 1 1-1z" fill="#8cc63f"/></svg>(555) 014-2290</li>
        <li><svg width="12" height="10" viewBox="0 0 12 10" fill="none" stroke="#8cc63f" stroke-width="1.4"><rect x="0.7" y="0.7" width="10.6" height="8.6"/><path d="M1 1l5 4 5-4"/></svg>care@medora-health.com</li>
      </ul>
    </div>
    <div class="contact-now">
      <h4>Contact Now</h4>
      <div class="contact-form">
        <div class="field">Name</div>
        <div class="field message">Type Your Message</div>
        <div class="field">Email</div>
        <div class="field">Subject</div>
        <a class="btn btn-submit">Submit</a>
      </div>
    </div>
  </div>
  <div class="footer-bar">
    <span>(c) 2015 - Medora. All Rights Reserved.</span>
    <div class="socials"><i></i><i></i><i></i><i></i></div>
  </div>
</footer>

</body>
</html>
```